Medical Learning Web Design Project

The web site will be a site for medical students. It is aimed at providing a collaborative place for students to study, learn, question each other and challenge each other with learning. The site needs to have a section on the page that is for the content and this needs to be relatively clean and clinical. The surrounding elements will be informative (for the statistics, challenge etc). There will also be a slide-out screen that allows for the social/friend elements of the site.

The colour scheme needs to be clean and clinical where appropriate, but also engaging and exciting for the social/competitive elements.
Updates

Just for clarity: The site isn't expected to be 'coded' ... it is just the layered PSD files that I need.

Also, with regards to the navigation buttons ... they will never ALL be present at the same time so don't feel the need to design all on one page, but creativity around allowing few or many on a page will be an advantage ...

Thanks

Hi,

Please note that the image uploaded has been done as a wireframe by the developers. I am looking for a more creative and engaging way of presenting that content ...

Thanks

Hi all

Thank you all for the designs so far ...!

Please have a look at the new uploaded file, I am also looking not just for a 'templated home page' but also some different layouts that are represented in these wireframes. If the various layouts represented can be condensed down into 1 or 2 page templates with appropriate colour schemes to capture the type of content on the page (as already mentioned ... social .. competitive ... learning), then that will help me live the concepts better too! The friends tab for instance I have envisaged as a slider covering the screen and then sliding back when complete ... but let me see what creativity you can give to this ...!

Many thanks

Reason: Just allowing for final tweaks ...

Target Market(s)

Medical Students

Industry/Entity Type

Medical

Requirements
Must have
• - Not cluttered appearance
- Dynamic navigation (ie. site will be developed to only show relevant navigation buttons on each page ...)
- Navigation buttons (need to be individual buttons) will be: 'Home', 'Take the tour', 'What your peers say', 'Subscriptions', 'Free Signup', 'Contact us', 'Moderation', 'Statistics', 'Competition', 'Answer Questions', 'Post Questions', 'My profile', 'Friends'
- Please also ensure it is engaging for social elements and competitive elements (perhaps slightly different design for pages focussed on each element)
- Please also ensure that there is a masculine design and feminine design that has continuity for the site but depending on gender the design can be tailored to be more appealing (that means perhaps male social design, male competitive design, female social design, female competitive design ... without loosing continuity through the site).
- Photoshop PSD format
- Pixel perfect at least 1000 pixels wide (but the design needs to allow for various monitor sizes (only desktop or laptops ... not tablets or smart phones)

```html
<!DOCTYPE html>
<html lang="en">
<head>
<meta charset="utf-8">
<title>Quizora – The Medical Peer Review</title>
<link href="https://fonts.googleapis.com/css2?family=Open+Sans:ital,wght@0,400;0,600;0,700;1,400&display=swap" rel="stylesheet">
<style>
:root{
  --page:#ffffff;
  --bar:#e9e9e9;
  --ink:#333333;
  --muted:#777777;
  --rule:#d8d8d8;
  --green-hi:#a9dc78;
  --green-lo:#6fb640;
  --green-ink:#1f4a0c;
  --brand-green:#5aa82c;
  --teal-hi:#7fd7db;
  --teal-lo:#3db0ba;
  --red-hi:#f58a8a;
  --red-lo:#e0464b;
  --orange:#f0a01e;
  --gold:#f5c248;
  --video:#1c1c1c;
  --chirp:#2f7fb5;
  --link:#3b5998;
}
*{box-sizing:border-box;margin:0;padding:0}
html,body{width:800px;height:1200px;overflow:hidden;background:var(--page)}
body{font-family:"Open Sans",Arial,sans-serif;color:var(--ink);font-size:9px}
.canvas{position:relative;width:800px;height:1200px;overflow:hidden}
.abs{position:absolute}

/* top bar */
.web-bar{left:0;top:0;width:800px;height:20px;background:var(--bar)}
.web-bar__label{left:568px;top:4px;font-size:9px;color:#555}
.web-bar__icons{left:660px;top:3px;display:flex;gap:4px}
.web-bar__icons span{width:14px;height:14px;border-radius:3px;display:block}

/* header */
.brand{left:112px;top:34px;width:100px;height:66px}
.brand__dot{position:absolute;left:32px;top:0;width:18px;height:18px;border-radius:50%;background:var(--brand-green)}
.brand__name{position:absolute;left:2px;top:22px;font-size:22px;font-weight:600;color:#6b6b6b;letter-spacing:-.5px}
.brand__tag{position:absolute;left:2px;top:54px;font-size:7px;color:#555;white-space:nowrap}
.quote{left:214px;top:40px;width:222px;font-size:9px;font-style:italic;line-height:12px;text-align:right;color:#333}
.quote span{display:block;text-align:left;white-space:nowrap;margin-left:-6px}
.login label{position:absolute;font-size:9px;color:#333}
.login .field{position:absolute;width:100px;height:15px;border:1px solid #bbb;background:#fff}
.login__btn{left:666px;top:56px;width:40px;height:16px;border-radius:8px;background:linear-gradient(#fbd679,var(--gold));border:1px solid #d9a530;font-size:9px;text-align:center;line-height:14px;color:#4a3000}
.login__remember{left:454px;top:77px;font-size:8.5px;display:flex;align-items:center;gap:5px}
.login__remember i{width:9px;height:9px;border:1px solid #999;display:block}
.login__forgot{left:560px;top:77px;font-size:8.5px;color:#333;text-decoration:underline}

/* nav */
.nav{left:89px;top:111px;width:618px;height:19px;display:flex;gap:3px}
.nav a{flex:auto;height:19px;border-radius:5px 5px 0 0;background:linear-gradient(var(--green-hi),var(--green-lo));color:var(--green-ink);font-size:9px;text-align:center;line-height:19px;text-decoration:none;letter-spacing:.3px}
.nav-rule{left:66px;top:130px;width:664px;height:3px;background:#e4e4e4}

/* slider */
.hero{left:89px;top:156px;width:620px;height:232px;border:1px solid #e2e2e2;background:#fff}
.hero__title{left:44px;top:34px;font-size:14px;font-weight:700;color:var(--orange)}
.hero__list{left:60px;top:68px;list-style:none;font-size:9.5px;line-height:22.5px;color:#333}
.hero__art{left:310px;top:20px;width:234px;height:196px;border-radius:50%/40%;background:radial-gradient(ellipse at 50% 60%,#d9ecef 0%,#eef4f5 55%,#fff 75%)}
.hero__arrow{top:46%;width:30px;height:30px;border-radius:50%;background:#e6e6e6}
.hero__arrow svg{display:block;margin:9px}
.hero__dots{left:278px;top:218px;display:flex;gap:4px}
.hero__dots i{width:8px;height:8px;border-radius:50%;background:#cfcfcf;display:block}

/* panels */
.panel{border:1px solid #dedede;border-radius:4px;background:#fff}
.panel__head{position:absolute;left:-1px;top:-1px;right:-1px;height:22px;border-radius:5px;color:#222;font-size:10px;line-height:22px;padding-left:12px}
.panel__head--red{background:linear-gradient(var(--red-hi),var(--red-lo));color:#3a0000}
.panel__head--teal{background:linear-gradient(var(--teal-hi),var(--teal-lo))}
.panel__head--side{height:23px;font-size:9.5px;padding-left:10px}
.panel__head--side svg{position:absolute;right:8px;top:8px}

.quiz{left:89px;top:412px;width:398px;height:136px}
.quiz__q{left:14px;top:36px;font-size:10px;font-weight:700}
.quiz__text{left:14px;top:52px;width:370px;font-size:8.5px;line-height:11.5px;color:#444}
.btn{position:absolute;height:20px;border-radius:8px;font-size:9.5px;font-weight:700;text-align:center;line-height:18px;border:1px solid #c8c8c8;background:linear-gradient(#fafafa,#dcdcdc)}
.btn--true{left:12px;top:98px;width:46px;color:#4f9b1b}
.btn--false{left:64px;top:98px;width:50px;color:#e0464b}
.btn--next{left:253px;top:98px;width:130px;color:#333}

.section-title{left:99px;top:568px;font-size:12.5px;font-weight:700}
.video{left:99px;top:593px;width:376px;height:228px;background:#ececec;border:1px solid #ccc}
.video__screen{position:absolute;left:0;top:0;width:374px;height:190px;background:var(--video)}
.video__more{position:absolute;left:138px;top:56px;font-size:7px;color:#555}
.video__time{position:absolute;top:194px;font-size:8px;color:#333}
.video__track{position:absolute;left:40px;top:198px;width:292px;height:4px;background:#bbb;border-radius:2px}
.video__track b{display:block;width:102px;height:4px;background:#555;border-radius:2px}
.video__knob{position:absolute;left:132px;top:195px;width:12px;height:10px;background:#888;border-radius:2px}
.video__controls{position:absolute;left:0;top:210px;width:374px;height:16px;display:flex;align-items:center;font-size:7.5px;color:#333;gap:12px;padding:0 6px;background:linear-gradient(#f4f4f4,#d8d8d8)}

.feature{top:844px;width:192px;height:260px}
.feature__art{position:absolute;left:28px;top:38px;width:136px;height:148px;border-radius:6px}
.feature__text{position:absolute;left:14px;top:188px;width:168px;font-size:8.5px;line-height:11.5px;color:#444}
.feature__more{position:absolute;right:12px;top:240px;font-size:8.5px;color:#444}

/* sidebar */
.side{left:511px;width:198px}
.fan{top:412px;height:72px}
.pill{position:absolute;height:13px;border:1px solid #b9c4d6;border-radius:3px;font-size:7.5px;line-height:11px;padding:0 4px;background:linear-gradient(#f6f8fb,#dfe4ee);color:#333;font-weight:700}
.count{position:absolute;height:13px;border:1px solid #ccc;font-size:7.5px;line-height:11px;padding:0 4px;background:#fff}
.fan__likes{position:absolute;left:50px;top:51px;font-size:7.5px;color:#333}
.sq{display:inline-block;width:9px;height:9px;background:var(--link);vertical-align:-1px;margin-right:3px}

.fb{top:491px;height:206px}
.fb__page{position:absolute;left:8px;top:34px;width:28px;height:28px;background:linear-gradient(#d23a3a,#8a1b1b)}
.fb__title{position:absolute;left:42px;top:33px;font-size:10px;font-weight:700;color:var(--link)}
.fb__title small{font-size:7px;font-weight:400;color:#555}
.fb__count{position:absolute;left:8px;top:73px;font-size:7.5px;color:#333}
.fb__grid{position:absolute;left:6px;top:86px;display:grid;grid-template-columns:repeat(5,34px);gap:4px 4px}
.fb__fan{font-size:6.5px;text-align:center;color:#555}
.fb__fan i{display:block;width:34px;height:34px;margin-bottom:2px}
.fb__plugin{position:absolute;left:8px;top:190px;font-size:7px;color:#555}

.chirp-head{top:707px;height:24px}
.chirp{left:511px;top:741px;width:198px;height:204px;background:var(--chirp);border-radius:4px}
.chirp__head{position:absolute;left:8px;top:6px;color:#fff;font-size:7.5px}
.chirp__head b{display:block;font-size:12px;line-height:15px}
.chirp__feed{position:absolute;left:4px;top:42px;width:190px;height:142px;background:#fff}
.tweet{position:absolute;left:0;width:190px;border-bottom:1px solid #e2e2e2;font-size:7.5px;line-height:9.5px;padding:0 4px 0 30px;height:47px}
.tweet i{position:absolute;left:4px;top:3px;width:20px;height:20px}
.tweet b{color:var(--chirp);font-weight:600}
.tweet a{color:var(--chirp);text-decoration:none}
.tweet small{display:block;color:#999;font-size:6.5px}
.chirp__foot{position:absolute;left:8px;top:188px;color:#fff;font-size:7.5px;width:184px;display:flex;justify-content:space-between}
.chirp__foot b{font-weight:700}

/* footer */
.footer{left:0;top:1140px;width:800px;height:60px;background:#e6e6e6;text-align:center}
.footer__links{margin-top:16px;font-size:8.5px;color:#333}
.footer__links span{padding:0 4px}
.footer__copy{margin-top:6px;font-size:8.5px;color:#333}
</style>
</head>
<body>
<div class="canvas">

  <div class="abs web-bar">
    <div class="abs web-bar__label">Quizora on the web:</div>
    <div class="abs web-bar__icons" aria-label="Social links">
      <span style="background:#4a66a0"></span><span style="background:#44aadd"></span><span style="background:#2f77b0"></span><span style="background:#5b8db8"></span><span style="background:#e34c8e"></span><span style="background:#4aa84a"></span><span style="background:#3a8fd8"></span><span style="background:#5a7fc0"></span><span style="background:#f08a24"></span>
    </div>
  </div>

  <header>
    <div class="abs brand">
      <div class="brand__dot"></div>
      <div class="brand__name">Quizora</div>
      <div class="brand__tag">The Medical Peer Review</div>
    </div>
    <p class="abs quote">“Quizora keeps me ahead of the gam,<br>constantly testing my knowledge...”<span>- Sam, doctor in training, Northfield University</span></p>
    <div class="login">
      <label style="left:454px;top:43px">Username:</label>
      <div class="field" style="left:454px;top:57px"></div>
      <label style="left:560px;top:43px">Password:</label>
      <div class="field" style="left:560px;top:57px"></div>
      <div class="abs login__btn">Login</div>
      <div class="abs login__remember"><i></i>Keep me signed in</div>
      <div class="abs login__forgot">Forgot your password?</div>
    </div>
  </header>

  <nav class="abs nav">
    <a>HOME</a><a>TAKE A TOUR</a><a>WHAT YOUR PEERS SAY</a><a>SUBSCRIPTION PLANS</a><a>FREE SIGNUP</a><a>CONTACT US</a>
  </nav>
  <div class="abs nav-rule"></div>

  <section class="abs hero">
    <h1 class="abs hero__title">Quizora - The Medical Peer Review</h1>
    <ul class="abs hero__list">
      <li>- Test your medical knowledge</li>
      <li>- Answer a vast array of medical questions</li>
      <li>- Earn trophies as your knowledge increases</li>
      <li>- Rate questions from peers</li>
      <li>- Ask your own questions</li>
      <li>- Link to your friends and check thier progress</li>
    </ul>
    <div class="abs hero__art" role="img" aria-label="Illustration of medical staff standing around a connected network"></div>
    <div class="abs hero__arrow" style="left:8px"><svg width="12" height="12" viewBox="0 0 12 12"><path d="M8 2L4 6l4 4" fill="none" stroke="#777" stroke-width="1.5"/></svg></div>
    <div class="abs hero__arrow" style="right:8px"><svg width="12" height="12" viewBox="0 0 12 12"><path d="M4 2l4 4-4 4" fill="none" stroke="#777" stroke-width="1.5"/></svg></div>
    <div class="abs hero__dots"><i></i><i></i><i></i><i></i><i></i></div>
  </section>

  <section class="abs panel quiz">
    <div class="panel__head panel__head--red">Answer a question!</div>
    <h2 class="abs quiz__q">Question 1. True or False</h2>
    <p class="abs quiz__text">Lorem Ipsum is simply dummy text of the printing and typesetting industry. Lorem Ipsum has been the industry's standard dummy text ever since the 1500s, when an unknown printer took...</p>
    <div class="btn btn--true">TRUE</div>
    <div class="btn btn--false">FALSE</div>
    <div class="btn btn--next">Try another question</div>
  </section>

  <h2 class="abs section-title">How Quizora Works</h2>
  <div class="abs video">
    <div class="video__screen">
      <span class="video__more">more...</span>
      <svg style="position:absolute;left:176px;top:78px" width="28" height="34" viewBox="0 0 28 34"><path d="M2 2l24 15L2 32z" fill="#666"/></svg>
    </div>
    <span class="video__time" style="left:8px">01:48</span>
    <div class="video__track"><b></b></div>
    <div class="video__knob"></div>
    <span class="video__time" style="left:346px">02:28</span>
    <div class="video__controls">
      <span>❚❚ PAUSE</span><span style="margin-left:auto">✉ email</span><span>⛓ get link</span><span>⊕ get code</span><span style="margin-left:10px">⤢</span><span>◀)</span><span>MENU</span>
    </div>
  </div>

  <section class="abs panel feature" style="left:89px">
    <div class="panel__head panel__head--teal">Statistics</div>
    <div class="feature__art" role="img" aria-label="Illustration of a colourful bar chart with a magnifying glass" style="background:linear-gradient(135deg,#f5e25a,#4ab5e8 45%,#e8504f 70%,#7ac943)"></div>
    <p class="feature__text">Lorem Ipsum is simply dummy text of the printing and typesetting industry. Lorem Ipsum has been the industry's standard dummy text ever since the 1500s, when an unknown printer took...</p>
    <span class="feature__more">more....</span>
  </section>

  <section class="abs panel feature" style="left:295px">
    <div class="panel__head panel__head--teal">Challenge</div>
    <div class="feature__art" role="img" aria-label="Illustration of a doctor pointing forward" style="background:linear-gradient(#f6e2cf,#eeeeee 60%,#dcdcdc)"></div>
    <p class="feature__text">Lorem Ipsum is simply dummy text of the printing and typesetting industry. Lorem Ipsum has been the industry's standard dummy text ever since the 1500s, when an unknown printer took...</p>
    <span class="feature__more">more....</span>
  </section>

  <aside>
    <section class="abs panel side fan">
      <div class="panel__head panel__head--teal panel__head--side">Become a fan of Quizora<svg width="8" height="6" viewBox="0 0 8 6"><path d="M0 0h8L4 6z" fill="#1b5a60"/></svg></div>
      <div class="pill" style="left:8px;top:32px">Follow @quizora</div>
      <div class="count" style="left:76px;top:32px">620K followers</div>
      <div class="pill" style="left:8px;top:50px">Like</div>
      <div class="fan__likes"><span class="sq"></span>856,735 people like this.</div>
    </section>

    <section class="abs panel side fb">
      <div class="panel__head panel__head--teal panel__head--side">Quizora on Friendbook<svg width="8" height="6" viewBox="0 0 8 6"><path d="M0 0h8L4 6z" fill="#1b5a60"/></svg></div>
      <div class="fb__page" role="img" aria-label="Page profile picture"></div>
      <div class="fb__title">ReelNotes.net <small>on Friendbook</small></div>
      <div class="pill" style="left:42px;top:48px">Like</div>
      <div class="fb__count">9,957 people like <b>ReelNotes.net</b>.</div>
      <div class="fb__grid">
        <div class="fb__fan"><i role="img" aria-label="Fan photo" style="background:#7a5a48"></i>Rowan</div>
        <div class="fb__fan"><i role="img" aria-label="Fan photo" style="background:#a3885e"></i>Gary</div>
        <div class="fb__fan"><i role="img" aria-label="Fan photo" style="background:#8c8f94"></i>Milo</div>
        <div class="fb__fan"><i role="img" aria-label="Fan photo" style="background:#c49a74"></i>Bruno</div>
        <div class="fb__fan"><i role="img" aria-label="Fan photo" style="background:#3f3a36"></i>Jonas</div>
        <div class="fb__fan"><i role="img" aria-label="Fan photo" style="background:#5e3a2a"></i>DJ</div>
        <div class="fb__fan"><i role="img" aria-label="Fan photo" style="background:#6d6b3a"></i>Kenji</div>
        <div class="fb__fan"><i role="img" aria-label="Fan photo" style="background:#b5523c"></i>Ella</div>
        <div class="fb__fan"><i role="img" aria-label="Fan photo" style="background:#9aa3a8"></i>Stanley</div>
        <div class="fb__fan"><i role="img" aria-label="Fan photo" style="background:#b88a2a"></i>Adaeze</div>
      </div>
      <div class="fb__plugin"><span class="sq"></span>Friendbook social plugin</div>
    </section>

    <section class="abs panel side chirp-head">
      <div class="panel__head panel__head--teal panel__head--side">Quizora on Chirper<svg width="8" height="6" viewBox="0 0 8 6"><path d="M0 0h8L4 6z" fill="#1b5a60"/></svg></div>
    </section>
    <div class="abs chirp">
      <div class="chirp__head">What's being said about<b>Port Haven</b></div>
      <div class="chirp__feed">
        <div class="tweet" style="top:2px"><i role="img" aria-label="User avatar" style="background:#8a6a50"></i><b>JonahReyes</b> I'm at Copper Kettle Roasters (48 Alder St, at 3rd, Port Haven). <a>http://lnk.ex/4r7q</a><small>3 minutes ago</small></div>
        <div class="tweet" style="top:50px"><i role="img" aria-label="User avatar" style="background:#6a7f8c"></i><b>lena_marsh</b> Trying to get some sleep before a 15 hour trip form Lundvik to Port Haven tomorrow. Moving to the U.S tomorrow!!!<small>2 minutes ago</small></div>
        <div class="tweet" style="top:98px;border:0"><i role="img" aria-label="User avatar" style="background:#a58a60"></i><b>pbrightwell</b> @ Harbor field in Port Haven w/ family.<small>about 1 minute ago</small></div>
      </div>
      <div class="chirp__foot"><b>Chirper</b><span>Join the conversation</span></div>
    </div>
  </aside>

  <footer class="abs footer">
    <div class="footer__links">Home<span>|</span>Take a tour<span>|</span>What your peers say<span>|</span>Subscription plans<span>|</span>Free Signup<span>|</span>Contact Us<span>|</span>Sitemap</div>
    <div class="footer__copy">Copyright 2012 Quizora Limited</div>
  </footer>

</div>
</body>
</html>
```